Website Revamp: Bravoly.com

Just got a new logo looking for a web design to go with the business. I need the photoshop files and stock photos. No Word Press Please.

```html
<!DOCTYPE html>
<html lang="en">
<head>
<meta charset="utf-8">
<title>Bravoly — Auto Recycling</title>
<link rel="stylesheet" href="https://fonts.googleapis.com/css2?family=Exo+2:wght@500;600;700&family=Roboto:wght@400;500&display=swap">
<style>
:root{
  --green:#6cb52f;
  --green-dark:#4e8f1e;
  --green-pale:#e5f3d8;
  --ink:#5c6467;
  --ink-dark:#2f3436;
  --body:#55595b;
  --footer:#4f5757;
  --white:#ffffff;
}
*{box-sizing:border-box;margin:0;padding:0}
html,body{width:1200px;height:3861px;overflow:hidden;background:var(--white)}
body{position:relative;font-family:"Roboto",Arial,sans-serif;color:var(--body)}
.abs{position:absolute}
.head-font{font-family:"Exo 2",Arial,sans-serif}

/* header */
.search{left:172px;top:21px;width:236px;height:39px;border:1px solid #d9dcdd;border-radius:20px;font-size:13px;color:#8d9294;padding:11px 15px}
.search svg{position:absolute;right:12px;top:10px}
.nav a{position:absolute;top:90px;font:500 14px "Roboto",sans-serif;color:var(--ink-dark);text-decoration:none}
.nav a.active{color:var(--green)}
.brand{left:520px;top:15px;width:160px;text-align:center}
.brand-mark{display:block;width:62px;height:62px;border-radius:50%;background:var(--green);margin:0 auto 4px}
.brand-name{font:700 22px "Exo 2",sans-serif;color:var(--green);letter-spacing:1px}
.call{left:770px;top:26px;font:600 24px "Exo 2",sans-serif;color:var(--green);display:flex;align-items:center;gap:8px}
.call-icon{width:32px;height:32px;border-radius:50%;background:var(--green);display:flex;align-items:center;justify-content:center}

/* hero */
.hero{left:0;top:126px;width:1200px;height:714px;background:linear-gradient(180deg,#3d4a57 0%,#5c6670 40%,#3a3f44 75%,#2a2d30 100%)}
.hero-title{left:0;top:375px;width:1200px;text-align:center;font:700 56px "Exo 2",sans-serif;color:var(--white);letter-spacing:-1px}
.btn{display:flex;align-items:center;justify-content:center;background:var(--green);color:var(--white);border-radius:30px;text-transform:uppercase;text-decoration:none}
.hero-btn{left:477px;top:456px;width:247px;height:40px;font:700 14px "Exo 2",sans-serif;border:2px solid #fff}
.arrow{top:395px}

/* about */
.section-title{font:700 48px "Exo 2",sans-serif;color:var(--ink);letter-spacing:-1px}
.section-title span{color:var(--green)}
.about-title{left:172px;top:920px}
.about-text{left:172px;top:1000px;width:432px;font-size:12.5px;line-height:21px;text-align:justify;color:var(--body)}
.about-btn{left:171px;top:1207px;width:153px;height:47px;font:500 15px "Roboto",sans-serif}
.about-badge{left:727px;top:938px;width:284px;height:284px;border-radius:50%;background:radial-gradient(circle at 50% 40%,#ffffff 0 45%,var(--green) 46% 100%);display:flex;align-items:center;justify-content:center;font:700 30px "Exo 2",sans-serif;color:var(--green-dark)}

/* services */
.services-bg{left:0;top:1327px;width:1200px;height:1330px;background:var(--green-pale)}
.services-photo{left:0;top:1327px;width:1200px;height:428px;background:linear-gradient(180deg,#4c5866 0%,#3b4149 55%,#2c3034 100%)}
.services-title{left:0;top:1428px;width:1200px;text-align:center;font:700 48px "Exo 2",sans-serif;color:var(--white)}
.service{border-radius:50%;border:12px solid var(--green);display:flex;align-items:center;justify-content:center;text-align:center;font:700 22px "Exo 2",sans-serif;color:var(--white);line-height:26px;text-transform:uppercase}
.service.side{width:286px;height:286px;background:#3a4046}
.service.main{width:324px;height:324px;background:radial-gradient(circle,#2f5a1c 0%,#244716 70%,#3f7a22 100%);border-color:var(--green);box-shadow:0 0 0 8px #2b5419 inset,0 10px 20px rgba(0,0,0,.25);font-size:24px}

/* why */
.why-title{left:0;top:1958px;width:1200px;text-align:center}
.card{width:413px;height:167px;background:var(--white);border-radius:84px;box-shadow:0 4px 18px rgba(80,120,40,.12)}
.card-icon{position:absolute;left:32px;top:28px;width:110px;height:110px;border-radius:50%;border:6px solid var(--green);border-right-color:#d8ebc6;display:flex;align-items:center;justify-content:center}
.card h3{position:absolute;left:165px;top:36px;font:600 20px "Exo 2",sans-serif;color:var(--ink-dark)}
.card p{position:absolute;left:165px;top:70px;width:205px;font-size:13px;line-height:21px;color:var(--body)}
.why-center{left:568px;top:2213px;width:66px;height:66px;border-radius:50%;background:var(--white);border:4px solid var(--green)}
.why-btn{left:508px;top:2470px;width:185px;height:53px;font:600 18px "Exo 2",sans-serif;text-transform:uppercase}

/* blog */
.blog-title{left:0;top:2664px;width:1200px;text-align:center}
.blog-feature{left:172px;top:2739px;width:470px;height:423px;border-radius:8px;background:linear-gradient(160deg,#5e6870 0%,#3d4a5c 50%,#2a3440 100%)}
.blog-over{left:210px;top:3022px;width:390px;height:163px;background:var(--white);border-radius:6px;box-shadow:0 6px 20px rgba(0,0,0,.12);padding:20px 36px}
.date{font:600 14px "Exo 2",sans-serif;color:var(--green);display:flex;align-items:center;gap:5px}
.blog-over h3{font:600 20px "Exo 2",sans-serif;color:var(--ink-dark);margin:10px 0 8px}
.blog-over p{font-size:12px;line-height:19px;color:var(--body)}
.post{left:671px;width:360px;height:129px;border:1px solid #dfe3e4;border-radius:6px;background:var(--white)}
.post-thumb{position:absolute;left:11px;top:11px;width:120px;height:106px;background:linear-gradient(150deg,#5d6871,#34404c 60%,#6c3a36)}
.post .date{position:absolute;left:145px;top:26px;font-size:12px}
.post h4{position:absolute;left:145px;top:44px;font:600 17px "Exo 2",sans-serif;color:var(--ink-dark)}
.post p{position:absolute;left:145px;top:72px;width:200px;font-size:10.5px;line-height:16px;color:var(--body)}

/* footer */
.footer-bg{left:0;top:3270px;width:1200px;height:591px}
.foot h5{font:600 17px "Exo 2",sans-serif;color:var(--white);display:flex;align-items:center;gap:8px}
.foot p,.foot li{font-size:12px;line-height:22px;color:#e4e7e8;list-style:none}
.foot li.small{font-size:11px}
.footer-brand{left:890px;top:3475px;width:125px;text-align:center}
.footer-brand .brand-mark{width:66px;height:66px;background:transparent;border:4px solid var(--white)}
.footer-brand .brand-name{color:var(--white);font-size:22px}
.socials{left:859px;top:3662px;display:flex;gap:26px}
.social{width:22px;height:22px;border-radius:50%;background:var(--white)}
.rule{left:172px;top:3789px;width:868px;height:1px;background:#69716f}
.copyright{left:0;top:3808px;width:1200px;text-align:center;font-size:13px;color:#e4e7e8}
</style>
</head>
<body>

<!-- header -->
<header>
  <div class="abs search">Search
    <svg width="18" height="18" viewBox="0 0 18 18"><circle cx="7.5" cy="7.5" r="6" fill="none" stroke="#9aa0a2" stroke-width="1.6"/><line x1="12" y1="12" x2="17" y2="17" stroke="#9aa0a2" stroke-width="1.6"/></svg>
  </div>
  <nav class="nav">
    <a class="active" style="left:180px">HOME</a>
    <a style="left:265px">ABOUT</a>
    <a style="left:352px">SERVICES</a>
    <a style="left:759px">REVIEWS</a>
    <a style="left:861px">BLOG</a>
    <a style="left:936px">CONTACT US</a>
  </nav>
  <div class="abs brand"><span class="brand-mark"></span><span class="brand-name">BRAVOLY</span></div>
  <div class="abs call">
    <span class="call-icon"><svg width="16" height="16" viewBox="0 0 24 24"><path d="M6.6 10.8a15 15 0 006.6 6.6l2.2-2.2a1 1 0 011-.25 11.4 11.4 0 003.6.6 1 1 0 011 1V20a1 1 0 01-1 1A17 17 0 013 4a1 1 0 011-1h3.5a1 1 0 011 1c0 1.25.2 2.45.57 3.57a1 1 0 01-.25 1z" fill="#fff"/></svg></span>
    Call: (555)-010-2748
  </div>
</header>

<!-- hero -->
<section>
  <div class="abs hero" role="img" aria-label="Photo of a scrap yard grapple lifting a dark car"></div>
  <svg class="abs" style="left:0;top:600px" width="1200" height="260" viewBox="0 0 1200 260">
    <path d="M0 60 C300 250 800 260 1090 100 L1200 80 L1200 260 L0 260 Z" fill="#fff"/>
    <path d="M0 60 C300 250 800 260 1090 100" fill="none" stroke="#6cb52f" stroke-width="14"/>
  </svg>
  <svg class="abs arrow" style="left:34px" width="36" height="66" viewBox="0 0 36 66"><polyline points="32,3 4,33 32,63" fill="none" stroke="#fff" stroke-width="4"/></svg>
  <svg class="abs arrow" style="left:1124px" width="36" height="66" viewBox="0 0 36 66"><polyline points="4,3 32,33 4,63" fill="none" stroke="#fff" stroke-width="4"/></svg>
  <h1 class="abs hero-title">WELCOME TO BRAVOLY</h1>
  <a class="abs btn hero-btn">Get your online quote</a>
</section>

<!-- about -->
<section>
  <h2 class="abs section-title about-title">ABOUT <span>BRAVOLY</span></h2>
  <p class="abs about-text">Sed ut perspiciatis unde omnis iste natus error sit voluptatem accusantium doloremque laudantium, totam rem aperiam, eaque ipsa quae ab illo inventore veritatis et quasi architecto beatae vitae dicta sunt explicabo. Nemo enim ipsam voluptatem quia voluptas sit aspernatur aut odit aut fugit, sed quia consequuntur magni dolores eos qui ratione voluptatem sequi nesciunt. NequeSed ut perspiciatis unde omnis iste natus error sit voluptatem accusantium doloremque laudantium, totam rem aperiam, eaque ipsa quae ab illo inventore veritatis et quasi architecto beatae vitae dicta sunt explicabo. Nemo enim ipsam voluptatem quia voluptas.</p>
  <a class="abs btn about-btn">READ MORE</a>
  <div class="abs about-badge">BRAVOLY</div>
</section>

<!-- services -->
<section>
  <div class="abs services-bg"></div>
  <div class="abs services-photo" role="img" aria-label="Photo of a scrap yard with a worker and crane at dusk"></div>
  <svg class="abs" style="left:0;top:1640px" width="1200" height="120" viewBox="0 0 1200 120">
    <path d="M0 115 C250 75 420 60 600 60 C780 60 950 75 1200 115 L1200 120 L0 120 Z" fill="#e5f3d8"/>
  </svg>
  <h2 class="abs services-title">OUR SERVICES</h2>
  <div class="abs service side" style="left:176px;top:1570px">AUSANTIUM<br>DOLOREM</div>
  <div class="abs service side" style="left:741px;top:1570px">AUSANTIUM<br>DOLOREM</div>
  <div class="abs service main" style="left:439px;top:1548px">AUSANTIUM<br>DOLOREM</div>
</section>

<!-- why choose us -->
<section>
  <h2 class="abs section-title why-title">WHY <span>CHOOSE US</span></h2>

  <div class="abs card" style="left:172px;top:2066px">
    <div class="card-icon"><svg width="46" height="40" viewBox="0 0 46 40"><rect x="2" y="8" width="26" height="22" fill="none" stroke="#5c6467" stroke-width="3"/><path d="M28 16h9l7 8v6H28z" fill="none" stroke="#5c6467" stroke-width="3"/><circle cx="11" cy="33" r="4" fill="#5c6467"/><circle cx="36" cy="33" r="4" fill="#5c6467"/></svg></div>
    <h3>Ausantium dolorem</h3>
    <p>Sed ut perspiciatis unde omnis iste natus error sit voluptatem accusantium doloremue</p>
  </div>
  <div class="abs card" style="left:612px;top:2066px">
    <div class="card-icon"><svg width="44" height="44" viewBox="0 0 44 44"><path d="M8 22a14 14 0 0124-10" fill="none" stroke="#5c6467" stroke-width="3"/><path d="M36 22a14 14 0 01-24 10" fill="none" stroke="#5c6467" stroke-width="3"/><rect x="13" y="19" width="18" height="8" rx="3" fill="#5c6467"/></svg></div>
    <h3>Ausantium dolorem</h3>
    <p>Sed ut perspiciatis unde omnis iste natus error sit voluptatem accusantium doloremue</p>
  </div>
  <div class="abs card" style="left:172px;top:2260px">
    <div class="card-icon"><svg width="46" height="44" viewBox="0 0 46 44"><circle cx="28" cy="12" r="9" fill="none" stroke="#5c6467" stroke-width="3"/><path d="M4 34h8l10 4 18-8" fill="none" stroke="#5c6467" stroke-width="3"/><rect x="2" y="30" width="6" height="10" fill="#5c6467"/></svg></div>
    <h3>Ausantium dolorem</h3>
    <p>Sed ut perspiciatis unde omnis iste natus error sit voluptatem accusantium doloremue</p>
  </div>
  <div class="abs card" style="left:612px;top:2260px">
    <div class="card-icon"><svg width="42" height="42" viewBox="0 0 42 42"><line x1="6" y1="6" x2="36" y2="36" stroke="#5c6467" stroke-width="5" stroke-linecap="round"/><line x1="36" y1="6" x2="6" y2="36" stroke="#5c6467" stroke-width="5" stroke-linecap="round"/></svg></div>
    <h3>Ausantium dolorem</h3>
    <p>Sed ut perspiciatis unde omnis iste natus error sit voluptatem accusantium doloremue</p>
  </div>
  <div class="abs why-center"></div>
  <a class="abs btn why-btn">Read more</a>
</section>

<!-- blog -->
<section>
  <svg class="abs" style="left:0;top:2580px" width="1200" height="80" viewBox="0 0 1200 80">
    <path d="M0 75 C300 10 900 10 1200 75 L1200 80 L0 80 Z" fill="#fff"/>
  </svg>
  <div class="abs" style="left:0;top:2655px;width:1200px;height:620px;background:#fff"></div>
  <h2 class="abs section-title blog-title">LATEST <span>BLOG</span></h2>
  <div class="abs blog-feature" role="img" aria-label="Photo of wrecked cars stacked in a scrap yard"></div>
  <article class="abs blog-over">
    <div class="date"><svg width="13" height="13" viewBox="0 0 13 13"><rect x="1" y="2" width="11" height="10" fill="none" stroke="#6cb52f" stroke-width="1.5"/><line x1="1" y1="5" x2="12" y2="5" stroke="#6cb52f" stroke-width="1.5"/></svg>May 29 2020</div>
    <h3>Lorem ipsum dolor sit amet</h3>
    <p>Lorem ipsum dolor sit amet, consectetur adipiscing elit, sed do eiusmod tempor incididunt ut labore et dolore magna aliqua. Ut enim ad minim veniam</p>
  </article>

  <article class="abs post" style="top:2739px">
    <div class="post-thumb" role="img" aria-label="Photo of a car engine bay"></div>
    <div class="date">May 28 2020</div>
    <h4>Finibuonorumlorum</h4>
    <p>Sed ut perspiciatis undloree omnis iste natus error sit voluptatem accusaloren</p>
  </article>
  <article class="abs post" style="top:2892px">
    <div class="post-thumb" role="img" aria-label="Photo of stacked scrap cars"></div>
    <div class="date">May 28 2020</div>
    <h4>Finibuonorumlorum</h4>
    <p>Sed ut perspiciatis undloree omnis iste natus error sit voluptatem accusaloren</p>
  </article>
  <article class="abs post" style="top:3039px">
    <div class="post-thumb" role="img" aria-label="Photo of damaged cars in a salvage yard"></div>
    <div class="date">May 28 2020</div>
    <h4>Finibuonorumlorum</h4>
    <p>Sed ut perspiciatis undloree omnis iste natus error sit voluptatem accusaloren</p>
  </article>
</section>

<!-- footer -->
<footer>
  <svg class="abs footer-bg" width="1200" height="591" viewBox="0 0 1200 591">
    <path d="M0 200 C250 60 650 0 1200 70 L1200 591 L0 591 Z" fill="#4f5757"/>
    <path d="M0 200 C250 60 650 0 1200 70" fill="none" stroke="#6cb52f" stroke-width="18"/>
  </svg>

  <div class="abs foot" style="left:174px;top:3483px">
    <h5><svg width="16" height="18" viewBox="0 0 16 18"><path d="M8 17s6-6 6-10A6 6 0 002 7c0 4 6 10 6 10z" fill="none" stroke="#fff" stroke-width="1.4"/><circle cx="8" cy="7" r="2" fill="#fff"/></svg>Address</h5>
    <p>Bravoly<br>Lorem ispmdumodr 1211,<br>4410 QT, loremusilslk<br>Veldhaven</p>
    <h5 style="margin-top:16px"><svg width="18" height="13" viewBox="0 0 18 13"><rect x="1" y="1" width="16" height="11" fill="none" stroke="#fff" stroke-width="1.4"/><polyline points="1,1 9,7 17,1" fill="none" stroke="#fff" stroke-width="1.4"/></svg>Email</h5>
    <p>info@bravoly.com</p>
    <h5 style="margin-top:16px"><svg width="16" height="16" viewBox="0 0 24 24"><path d="M6.6 10.8a15 15 0 006.6 6.6l2.2-2.2a1 1 0 011-.25 11.4 11.4 0 003.6.6 1 1 0 011 1V20a1 1 0 01-1 1A17 17 0 013 4a1 1 0 011-1h3.5a1 1 0 011 1c0 1.25.2 2.45.57 3.57a1 1 0 01-.25 1z" fill="none" stroke="#fff" stroke-width="1.6"/></svg>Phone</h5>
    <p>010-5550148</p>
  </div>

  <div class="abs foot" style="left:400px;top:3483px">
    <h5>Links</h5>
    <ul><li>Lorem ipsum dol adipiscin</li><li>Do eiusmodtem ipsum dolor</li><li>Consectetur adipiscin</li></ul>
    <h5 style="margin-top:22px">Information</h5>
    <ul><li class="small">About Bravoly</li><li class="small">Imprint</li><li class="small">Contact</li><li class="small">News</li></ul>
  </div>

  <div class="abs foot" style="left:662px;top:3483px">
    <h5>What We Do</h5>
    <ul><li>Lorem ipsum dolor</li><li>Consectetur adipiscin</li><li>Do eiusmodt</li><li>Lorem ipsum dolor</li><li>Consectetur adipiscin</li><li>Do eiusmodt</li><li>Lorem ipsum dolor</li><li>Consectetur adipiscin</li><li>Do eiusmodt</li></ul>
  </div>

  <div class="abs footer-brand"><span class="brand-mark"></span><span class="brand-name">BRAVOLY</span></div>
  <div class="abs foot" style="left:859px;top:3625px"><h5>Follow Us</h5></div>
  <div class="abs socials">
    <span class="social" aria-label="Social profile 1"></span>
    <span class="social" aria-label="Social profile 2"></span>
    <span class="social" aria-label="Social profile 3"></span>
    <span class="social" aria-label="Social profile 4"></span>
  </div>

  <div class="abs rule"></div>
  <p class="abs copyright">© 2020 Bravoly. All rights reserved.</p>
</footer>

</body>
</html>
```